Bicycle Tour Schedule on a Business Card

Need to develop a 2 side business card that highlights a series of bike tours on 1 side and a series of events on the other side.
This will be inserted into a card wallet that attaches to a cell phone and will be handed out at an expo. The card wallets are black and red so color must coordinate with both. There is a photo of the card wallets attached.

1 side needs to be devoted to Pedal Vista Trek and the others to KQR Venture events on the other. Dates and websites are very important.

Target Market(s)

Cyclists
Predominantly men ages 40+
Educated, Professionals

Industry/Entity Type

Business

Font styles to use
Serif

Requirements
Must have
• Pedal vista treks logo on 1 side and KQR Venture logo on the other side
• dates and websites clearly visible
• Design of both sides must go together.
• Must be portrait not landscape

```html
<!DOCTYPE html>
<html lang="en">
<head>
<meta charset="utf-8">
<title>Pedal Vista Treks &amp; KQR Venture – Event Cards</title>
<link rel="stylesheet" href="https://fonts.googleapis.com/css2?family=Source+Sans+3:ital,wght@0,400;0,600;0,700;1,700&display=swap">
<style>
  :root {
    --backdrop: #e4e4e4;
    --card: #f1f1f2;
    --ink: #4a4a4c;
    --ink-strong: #3b3b3d;
    --tour-blue: #1f4fa0;
    --tour-green: #3a9a4a;
    --event-red: #c3172f;
    --venture-teal: #1e6f9a;
  }
  * { box-sizing: border-box; margin: 0; padding: 0; }
  html, body {
    width: 1105px;
    height: 1200px;
    overflow: hidden;
    background: var(--backdrop);
    font-family: "Source Sans 3", "Myriad Pro", Arial, sans-serif;
    color: var(--ink);
  }
  .sheet {
    position: relative;
    width: 1105px;
    height: 1200px;
  }
  .card {
    position: absolute;
    top: 268px;
    width: 400px;
    height: 697px;
    background: var(--card);
    text-align: center;
  }
  .card--tours { left: 113px; }
  .card--events { left: 596px; }

  /* Brand lockups */
  .brand {
    display: flex;
    align-items: center;
    justify-content: center;
    gap: 12px;
    font-weight: 700;
    font-size: 32px;
    line-height: 1;
    letter-spacing: 0.2px;
  }
  .brand__mark { flex: none; }
  .card--tours .brand { margin-top: 92px; color: var(--tour-blue); }
  .card--events .brand { margin-top: 80px; color: var(--venture-teal); flex-direction: column; gap: 18px; }

  /* Taglines */
  .tagline {
    font-weight: 700;
    font-style: italic;
    font-size: 21px;
    line-height: 1.22;
  }
  .card--tours .tagline { color: var(--tour-blue); margin-top: 72px; padding: 0 30px; }
  .card--events .tagline { color: var(--event-red); margin-top: 34px; }

  /* Schedule list */
  .schedule { list-style: none; }
  .card--tours .schedule { margin-top: 44px; }
  .card--events .schedule { margin-top: 14px; }
  .schedule__item { margin-bottom: 22px; }
  .card--events .schedule__item { margin-bottom: 16px; }
  .schedule__name {
    display: block;
    font-size: 18.5px;
    font-weight: 400;
    line-height: 1.2;
  }
  .schedule__detail {
    display: block;
    font-size: 19px;
    font-weight: 700;
    color: var(--ink-strong);
    line-height: 1.2;
  }
</style>
</head>
<body>
<main class="sheet">

  <section class="card card--tours" aria-label="Pedal Vista Treks tour schedule">
    <div class="brand">
      <svg class="brand__mark" width="26" height="26" viewBox="0 0 26 26" aria-hidden="true">
        <circle cx="13" cy="13" r="13" fill="var(--tour-green)"/>
      </svg>
      <span class="brand__name">Pedal Vista Treks</span>
    </div>

    <p class="tagline">Fully supported bike tours.<br>Discover the hidden gems on<br>two wheels</p>

    <ul class="schedule">
      <li class="schedule__item">
        <span class="schedule__name">Heart of Colorado</span>
        <span class="schedule__detail">June 26 - July 2, 2016</span>
      </li>
      <li class="schedule__item">
        <span class="schedule__name">Colorado Front Range Tour</span>
        <span class="schedule__detail">August 14-20, 2016</span>
      </li>
      <li class="schedule__item">
        <span class="schedule__name">Cape Cod Tour</span>
        <span class="schedule__detail">October 9 -15, 2016</span>
      </li>
      <li class="schedule__item">
        <span class="schedule__name">Florida Key Tours</span>
        <span class="schedule__detail">November 6-12, 2016 &amp;</span>
        <span class="schedule__detail">December 4-10, 2016</span>
      </li>
    </ul>
  </section>

  <section class="card card--events" aria-label="KQR Venture event schedule">
    <div class="brand">
      <svg class="brand__mark" width="72" height="72" viewBox="0 0 72 72" aria-hidden="true">
        <rect width="72" height="72" fill="var(--event-red)"/>
      </svg>
      <span class="brand__name">KQR Venture</span>
    </div>

    <p class="tagline">Tri Spoke Series:<br>Cycling camps for youth</p>

    <ul class="schedule">
      <li class="schedule__item">
        <span class="schedule__name">Mountain Bike Camp</span>
        <span class="schedule__detail">July 8-10, 2016</span>
      </li>
      <li class="schedule__item">
        <span class="schedule__name">Cyclocross Camp</span>
        <span class="schedule__detail">August 26-28, 2016</span>
        <span class="schedule__detail">Trispokeseries.org</span>
      </li>
      <li class="schedule__item">
        <span class="schedule__name">Mile High Hundred Ride</span>
        <span class="schedule__detail">June 18, 2016</span>
        <span class="schedule__detail">Milehighhundred.com</span>
      </li>
      <li class="schedule__item">
        <span class="schedule__name">Colorado Trail 2 Trail Challenge</span>
        <span class="schedule__detail">July 30, 2016 - Cotrail2trail.com</span>
      </li>
      <li class="schedule__item">
        <span class="schedule__name">Zany Wheel Ride</span>
        <span class="schedule__detail">September 11, 2016</span>
        <span class="schedule__detail">zanywheelride.com</span>
      </li>
    </ul>
  </section>

</main>
</body>
</html>
```